Tovimar Community Development Planning New web site

Design a new web site. I have a budget of $1,500.00.
Attached on PowerPoint is a complete site plan. Home page and linked pages.
10 - 12 pages. All copy and photos will be supplied. (300dpi)
I have shown them the concept which they like.
No data bases required. Home page with animations dissolving.
They former web site has been taken down. They have been in business 30 years in New Jersey
Colors teal blues and greens
There will be a new logo)being designed)
The text in home page copy will give you a detailed story what they are all about.

files have been approved for Tovimar, Inc.   Brenton is the designer

```html
<!DOCTYPE html>
<html lang="en">
<head>
<meta charset="utf-8">
<title>Tovimar, Inc. — Community Development Planning</title>
<link href="https://fonts.googleapis.com/css2?family=Open+Sans:wght@400;600&family=Arimo:ital,wght@0,400;1,400&display=swap" rel="stylesheet">
<style>
:root{
  --blue:#1e73c0;
  --blue-dark:#1a5fa5;
  --nav-top:#3f8fd2;
  --nav-bottom:#1f6cb4;
  --nav-active:#6aa9de;
  --ink:#4a4a4a;
  --ink-soft:#666;
  --orange:#ec6a1f;
  --band:#f0f2f4;
  --card-line:#cfd3d8;
  --footer-top:#3a3a3a;
  --footer-bottom:#1c1c1c;
  --purple:#3a2664;
}
*{margin:0;padding:0;box-sizing:border-box}
html,body{width:915px;height:1200px;overflow:hidden;background:#fff}
body{position:relative;font-family:"Arimo",Arial,sans-serif;color:var(--ink)}
.abs{position:absolute}

.top-strip{left:0;top:0;width:915px;height:12px;background:#e3e3e3}
.site-header{left:0;top:12px;width:915px;height:62px;background:#fff}
.brand{left:133px;top:30px;font-family:"Open Sans",sans-serif;font-size:24px;color:var(--blue);font-weight:400;letter-spacing:.3px}
.contact{top:37px;font-family:"Open Sans",sans-serif;font-size:11px;color:#333;display:flex;align-items:center;gap:5px;white-space:nowrap}
.social{top:34px;width:21px;height:21px;border-radius:3px}

.main-nav{left:0;top:74px;width:915px;height:44px;background:linear-gradient(var(--nav-top),var(--nav-bottom))}
.main-nav ul{list-style:none;display:flex;position:absolute;left:131px;top:0;height:44px}
.main-nav li{font-family:"Open Sans",sans-serif;font-size:12.5px;color:#fff;padding:0 14px;line-height:44px;border-right:1px solid rgba(0,0,0,.18)}
.main-nav li.active{background:var(--nav-active)}
.main-nav li:last-child{border-right:none}

.hero{left:0;top:118px;width:915px;height:363px;overflow:hidden;background:radial-gradient(ellipse at 50% 45%,#f4f4f4 0%,#dadada 75%,#c8c8c8 100%)}
.hero-art{left:170px;top:-10px;width:600px;height:383px;background:radial-gradient(ellipse at 50% 45%,#f08a2a 0%,#e67718 45%,rgba(230,119,24,.35) 62%,rgba(230,119,24,0) 74%)}
.hero-cta{left:370px;top:221px;width:175px;height:49px;border-radius:6px;background:var(--purple);color:#fff;font-family:"Open Sans",sans-serif;font-size:21px;font-weight:600;text-align:center;line-height:49px;letter-spacing:.5px}
.dots{left:421px;top:322px;display:flex;gap:5px}
.dots span{width:11px;height:11px;border-radius:50%;background:#eee;border:2px solid #9a9a9a}
.dots span:first-child{background:#555}

.services{left:0;top:481px;width:915px;height:197px;background:linear-gradient(#fafbfc,#e4e8ec)}
.card{width:296px;height:70px;background:linear-gradient(#fff,#f1f1f1);border:1px solid var(--card-line)}
.card h3{position:absolute;left:25px;top:8px;font-size:11px;font-weight:400;color:var(--blue);font-family:"Arimo",Arial,sans-serif;letter-spacing:.2px}
.card p{position:absolute;left:25px;top:25px;width:262px;font-size:8px;line-height:11px;color:#777}
.card .more{position:absolute;right:15px;bottom:5px;width:42px;height:13px;background:linear-gradient(#3c9ae0,#1c6fc0);color:#fff;font-size:6.5px;text-align:center;line-height:13px}
.badge{width:40px;height:40px;border-radius:50%;background:#2b2b2b;border:2px solid #fff;box-shadow:0 0 0 1px #ccc}

.section-title{font-family:"Arimo",Arial,sans-serif;font-size:16px;color:var(--blue);font-weight:400}
.welcome-photo{left:131px;top:727px;width:325px;height:140px;background:linear-gradient(120deg,#dfe8ef,#b9c7d3 45%,#8fa0b0 70%,#e8ecef)}
.welcome-text{left:131px;top:873px;width:322px;font-size:9.2px;line-height:14px;color:var(--ink);text-align:justify}
.read-more{left:381px;top:931px;font-size:9.5px;font-style:italic;color:var(--blue)}
.results{left:475px;top:725px;width:306px;list-style:none}
.results li{position:relative;padding-left:20px;font-size:8.8px;line-height:13.6px;color:var(--ink);text-align:justify;margin-bottom:13.5px}
.results li svg{position:absolute;left:0;top:1px}

.memberships{left:0;top:970px;width:915px;height:126px;background:#f1f1f1}
.member{top:1048px;font-family:"Open Sans",sans-serif;font-size:11px;color:#1f3f70;display:flex;align-items:center;gap:8px}
.member .mark{width:28px;height:28px;background:#2e73b8}
.member small{display:block;font-size:7px;color:#555}

.site-footer{left:0;top:1096px;width:915px;height:104px;background:linear-gradient(var(--footer-top),var(--footer-bottom))}
.footer-links{left:134px;top:1126px;font-size:8.8px;color:#fff;font-family:"Arimo",Arial,sans-serif}
.footer-links span{padding:0 4px}
.copyright{left:135px;top:1147px;font-size:8.5px;color:#ddd}
.footer-social{top:1129px;width:25px;height:25px;border-radius:50%;border:2px solid #ddd}
.page-code{left:880px;top:1168px;font-size:7px;color:#ccc}
</style>
</head>
<body>

<div class="abs top-strip"></div>
<header class="abs site-header"></header>
<div class="abs brand">TOVIMAR, INC.</div>

<div class="abs contact" style="left:434px">
  <svg width="10" height="10" viewBox="0 0 10 10"><path d="M2 1l2 2-1 1.5c.6 1.2 1.3 1.9 2.5 2.5L7 6l2 2-1.2 1.5C4.5 9.3.7 5.5.5 2.2z" fill="#2d6fb5"/></svg>(555) 014-2290
</div>
<div class="abs contact" style="left:535px">
  <svg width="14" height="10" viewBox="0 0 14 10"><rect x=".5" y=".5" width="13" height="9" fill="none" stroke="#2d6fb5"/><path d="M.5.5l6.5 5 6.5-5" fill="none" stroke="#2d6fb5"/></svg>mail@tovimar.net
</div>
<div class="abs contact" style="left:657px">
  <svg width="10" height="12" viewBox="0 0 10 12"><circle cx="5" cy="3" r="2.6" fill="#2d6fb5"/><path d="M0 12c0-4 2-6 5-6s5 2 5 6z" fill="#2d6fb5"/></svg>Log in
</div>
<div class="abs social" style="left:711px;background:#5fb4e6" aria-label="Social profile 1"></div>
<div class="abs social" style="left:736px;background:#3b62a8" aria-label="Social profile 2"></div>
<div class="abs social" style="left:761px;background:#3a3a3a" aria-label="Social profile 3"></div>

<nav class="abs main-nav">
  <ul>
    <li class="active">HOME</li>
    <li>OUR COMPANY</li>
    <li>HOUSING REHAB APPLICATION</li>
    <li>AFFORDABLE APPLICATION</li>
    <li>CONTACT US</li>
  </ul>
</nav>

<section class="abs hero">
  <div class="abs hero-art" role="img" aria-label="Orange jigsaw puzzle pieces forming the word Community"></div>
  <div class="abs hero-cta">CLICK HERE</div>
  <div class="abs dots"><span></span><span></span><span></span><span></span><span></span></div>
</section>

<section class="abs services"></section>

<div class="abs card" style="left:159px;top:502px">
  <h3>COMMUNITY DEVELOPMENT PLANNING</h3>
  <p>Tovimar, Inc stands for Community, Grants, Planning and Housing. We specialize in all aspects of affordable housing, planning, SCFH</p>
  <span class="more">MORE</span>
</div>
<div class="abs badge" style="left:134px;top:515px">
  <svg width="36" height="36" viewBox="0 0 36 36"><rect x="11" y="12" width="9" height="13" fill="#fff"/><circle cx="15" cy="9" r="3" fill="#fff"/><rect x="20" y="15" width="6" height="6" fill="#fff"/></svg>
</div>

<div class="abs card" style="left:486px;top:501px">
  <h3>HOUSING REHABILITATION ADMINISTRATION</h3>
  <p>Tovimar, Inc stands for Community, Grants, Planning and Housing. We specialize in all aspects of affordable housing, planning, SCFH</p>
  <span class="more">MORE</span>
</div>
<div class="abs badge" style="left:462px;top:515px">
  <svg width="36" height="36" viewBox="0 0 36 36"><circle cx="12" cy="14" r="2.5" fill="#fff"/><circle cx="18" cy="12" r="2.5" fill="#fff"/><circle cx="24" cy="14" r="2.5" fill="#fff"/><rect x="8" y="19" width="20" height="6" rx="2" fill="#fff"/></svg>
</div>

<div class="abs card" style="left:159px;top:585px">
  <h3>NATIONAL HOUSING BUREAU PROGRAMS</h3>
  <p>Tovimar, Inc stands for Community, Grants, Planning and Housing. We specialize in all aspects of affordable housing, planning, SCFH</p>
  <span class="more">MORE</span>
</div>
<div class="abs badge" style="left:134px;top:599px">
  <svg width="36" height="36" viewBox="0 0 36 36"><rect x="10" y="9" width="11" height="17" fill="none" stroke="#fff" stroke-width="2"/><rect x="12" y="11" width="7" height="3" fill="#fff"/><path d="M22 26l6-8" stroke="#fff" stroke-width="1.5"/><circle cx="23" cy="19" r="1.5" fill="#fff"/><circle cx="27" cy="25" r="1.5" fill="#fff"/></svg>
</div>

<div class="abs card" style="left:486px;top:584px">
  <h3>IMPLEMENTATION OF PROGRAMS</h3>
  <p>Tovimar, Inc stands for Community, Grants, Planning and Housing. We specialize in all aspects of affordable housing, planning, SCFH</p>
  <span class="more">MORE</span>
</div>
<div class="abs badge" style="left:462px;top:597px">
  <svg width="36" height="36" viewBox="0 0 36 36"><circle cx="13" cy="10" r="2.5" fill="#fff"/><rect x="10" y="14" width="6" height="11" fill="#fff"/><circle cx="21" cy="21" r="6" fill="none" stroke="#fff" stroke-width="1.8"/><text x="21" y="24.5" font-size="9" fill="#fff" text-anchor="middle" font-family="Arimo,sans-serif">$</text></svg>
</div>

<h2 class="abs section-title" style="left:131px;top:697px">WELCOME TO TOVIMAR,INC.</h2>
<div class="abs welcome-photo" role="img" aria-label="Construction team in hard hats reviewing plans together"></div>
<p class="abs welcome-text">Tovimar, Inc. is a city planning firm that specializes in community development and housing rehabilitation program planning, design and implementation. We have over twenty years of experience in developing and administering income ing and Urban Development (NHB) and State Council on Fair Housing (SCFH) rules and regulations,</p>
<span class="abs read-more">READ MORE &gt;&gt;</span>

<h2 class="abs section-title" style="left:477px;top:697px">WE GET RESULTS</h2>
<ul class="abs results">
  <li><svg width="12" height="12" viewBox="0 0 12 12"><circle cx="6" cy="6" r="6" fill="var(--orange)"/><path d="M3 6l2 2 4-4" fill="none" stroke="#fff" stroke-width="1.6"/></svg>Tovimar designs income based programs to be supported by federal placement lotteries state funding.</li>
  <li><svg width="12" height="12" viewBox="0 0 12 12"><circle cx="6" cy="6" r="6" fill="var(--orange)"/><path d="M3 6l2 2 4-4" fill="none" stroke="#fff" stroke-width="1.6"/></svg>We implement local programs to benefit people seeking access to affordable housing.</li>
  <li><svg width="12" height="12" viewBox="0 0 12 12"><circle cx="6" cy="6" r="6" fill="var(--orange)"/><path d="M3 6l2 2 4-4" fill="none" stroke="#fff" stroke-width="1.6"/></svg>Our experienced staff screen applicants for local affordable housing.</li>
  <li><svg width="12" height="12" viewBox="0 0 12 12"><circle cx="6" cy="6" r="6" fill="var(--orange)"/><path d="M3 6l2 2 4-4" fill="none" stroke="#fff" stroke-width="1.6"/></svg>We pre-qualify persons who have applied for housing rehabilitation.</li>
  <li><svg width="12" height="12" viewBox="0 0 12 12"><circle cx="6" cy="6" r="6" fill="var(--orange)"/><path d="M3 6l2 2 4-4" fill="none" stroke="#fff" stroke-width="1.6"/></svg>Conduct placement lotteries</li>
  <li><svg width="12" height="12" viewBox="0 0 12 12"><circle cx="6" cy="6" r="6" fill="var(--orange)"/><path d="M3 6l2 2 4-4" fill="none" stroke="#fff" stroke-width="1.6"/></svg>Through local housing rehabilitation programs, our experience con-struction inspectors determine what improvements are required at eligible units based on local building codes and health and safety</li>
</ul>

<section class="abs memberships"></section>
<h2 class="abs section-title" style="left:404px;top:986px">MEMBERSHIPS</h2>
<div class="abs member" style="left:148px"><span class="mark"></span><span>Civic Growth Alliance<small>National network of community builders</small></span></div>
<div class="abs member" style="left:354px"><span class="mark"></span><span>Regional Planning Society<small>Garden Chapter</small></span></div>
<div class="abs member" style="left:573px"><span>State Zoning Officials Council<small>Association of local planning and zoning boards</small></span></div>

<footer class="abs site-footer"></footer>
<div class="abs footer-links">Home<span>|</span>Profile<span>|</span>Investment process<span>|</span>Investment solutions<span>|</span>News &amp; view<span>|</span>Contact</div>
<div class="abs copyright">Copyright © 2014 &nbsp;All rights reserved.</div>
<div class="abs footer-social" style="left:632px;background:#4aa8d8"></div>
<div class="abs footer-social" style="left:663px;background:#3b5da0"></div>
<div class="abs footer-social" style="left:694px;background:#555"></div>
<div class="abs footer-social" style="left:726px;background:#d9508f"></div>
<div class="abs footer-social" style="left:757px;background:#fff"></div>
<div class="abs page-code">C6</div>

</body>
</html>
```